Brevlon Website Design - Wordpress

Need a website WordPress design for our existing website that we just stood up. The logo is already in place and name. Brevlon.example We are a company which makes connections with our clients through educating them and providing networking events. We would like for the website to show a VIP/special feel to it.

Target Market(s)

Business executives and employees. Age group 26-65 in the following sectors:
- Technology
- Human Resources
- Finance
- Sales

Industry/Entity Type

Technical Service

Number of Pages Required

4 page

Font styles to use
Sans Serif

Requirements
Must have
• Must be something for Wordpress
Nice to have
• Would like this to be professional but look cutting edge and VIP.

```html
<!DOCTYPE html>
<html lang="en">
<head>
<meta charset="utf-8">
<title>Brevlon — Expand Your Business</title>
<link href="https://fonts.googleapis.com/css2?family=Poppins:wght@400;500;600;700&family=Open+Sans:wght@400;600&display=swap" rel="stylesheet">
<style>
:root{
  --navy:#0b1a38;
  --deep:#071227;
  --blue:#123a7a;
  --purple:#4a2470;
  --purple-soft:#c8b3d6;
  --yellow:#e8a21e;
  --yellow-soft:#f0d48f;
  --red:#c8192a;
  --ink:#1b1b1b;
  --grey:#555;
  --white:#fff;
  --accent-blue:#1f5fa8;
  --soul:#7a3d8c;
  --strength:#e0a020;
}
*{box-sizing:border-box;margin:0;padding:0}
html,body{width:1200px;height:4091px;overflow:hidden}
body{position:relative;background:var(--white);font-family:"Open Sans",Arial,sans-serif;color:var(--ink)}
.abs{position:absolute}
h1,h2,h3,.heading{font-family:"Poppins",Arial,sans-serif}

/* header */
.site-header{position:absolute;left:0;top:0;width:1200px;height:145px;background:var(--white)}
.brand{position:absolute;left:90px;top:40px;display:flex;align-items:center;gap:12px}
.brand-mark{width:26px;height:26px;background:var(--purple)}
.brand-name{font-family:"Poppins",sans-serif;font-weight:500;font-size:34px;color:var(--navy);letter-spacing:2px}
.main-nav{position:absolute;top:48px;left:518px;display:flex;gap:46px;font-family:"Poppins",sans-serif;font-size:19px;color:var(--ink)}
.login-btn{position:absolute;left:1010px;top:47px;width:100px;height:30px;background:var(--navy);color:var(--white);font-size:16px;text-align:center;line-height:30px;border-right:6px solid var(--yellow);border-radius:3px}

/* hero */
.hero{position:absolute;left:0;top:145px;width:1200px;height:640px;background:radial-gradient(circle at 75% 40%,#1e5b8c 0%,#0c2340 45%,#050d1c 100%)}
.hero-art{position:absolute;left:620px;top:30px;width:440px;height:540px;background:radial-gradient(circle at 55% 45%,#3fb6c9 0%,#1a6a86 40%,rgba(10,30,60,0) 72%)}
.hero-title{position:absolute;left:90px;top:205px;color:var(--white);font-weight:700;font-size:45px;line-height:1.1}
.hero-sub{position:absolute;left:90px;top:262px;color:var(--white);font-weight:600;font-size:31px}
.hero-dots{position:absolute;left:1160px;top:225px;display:flex;flex-direction:column;gap:16px}
.hero-dots span{width:7px;height:7px;border-radius:50%;background:rgba(255,255,255,.6)}

/* offer */
.section-title{position:absolute;width:1200px;text-align:center;font-family:"Poppins",sans-serif;font-weight:500;color:var(--ink)}
.section-sub{position:absolute;width:1200px;text-align:center;font-size:17px;color:var(--ink)}
.offer-item{position:absolute;width:260px;text-align:center}
.offer-icon{position:relative;width:120px;height:120px;margin:0 auto}
.offer-icon .tri{position:absolute;left:0;top:0}
.offer-icon .glyph{position:absolute;left:30px;top:12px;width:60px;height:92px;background:#2a2a2a;border-radius:8px;opacity:.85}
.offer-item h3{font-weight:500;font-size:21px;margin-top:36px;letter-spacing:.5px}
.offer-item p{font-size:13.5px;line-height:22px;color:var(--grey);margin-top:10px;height:44px;overflow:hidden}
.offer-item .more{margin-top:14px}

/* about */
.about-text{position:absolute;left:150px;top:1565px;width:900px;text-align:center;color:var(--white);font-size:15.5px;line-height:27px}
.pill-btn{position:absolute;background:var(--white);color:var(--ink);border-radius:18px;text-align:center;font-size:16px}

/* value */
.value-circle{position:absolute;left:428px;top:2130px;width:344px;height:344px;border-radius:50%;background:var(--white);box-shadow:0 0 22px rgba(0,0,0,.18);display:flex;align-items:center;justify-content:center;gap:12px}
.value-circle .brand-mark{width:34px;height:34px}
.value-circle .brand-name{font-size:40px}
.value-item{position:absolute;width:280px;font-size:14.5px;line-height:21px;color:#333}
.value-item h3{font-weight:500;font-size:22px;margin-bottom:6px}
.value-item.right{text-align:right}
.value-icon{position:absolute;width:40px;height:40px}

/* contact */
.field{position:absolute;height:53px;border:1.5px solid rgba(255,255,255,.8);border-radius:4px;color:var(--white);font-size:16px;padding:15px 18px}

/* events */
.event-card{position:absolute;width:324px;height:350px}
.event-photo{width:324px;height:208px}
.event-body{position:absolute;left:22px;top:168px;width:280px;height:180px;background:var(--white);box-shadow:0 2px 10px rgba(0,0,0,.18);text-align:center;padding-top:16px}
.event-date{font-size:13px;color:var(--red)}
.event-body h3{font-weight:600;font-size:16px;margin-top:10px}
.event-body p{font-size:13px;line-height:20px;color:var(--grey);margin-top:6px}
.red-btn{display:inline-block;margin-top:12px;width:114px;height:28px;background:var(--red);color:var(--white);font-size:13px;line-height:28px;border-radius:2px}

/* footer */
.site-footer{position:absolute;left:0;top:3790px;width:1200px;height:301px;background:#000;color:var(--white)}
.footer-col{position:absolute;top:52px;font-size:13px}
.footer-col h4{font-family:"Poppins",sans-serif;font-weight:500;font-size:15px;margin-bottom:14px;letter-spacing:.5px}
.footer-col li{list-style:none;line-height:22px}
.footer-col li::before{content:"▸ ";font-size:10px}
.contact-line{display:flex;gap:10px;align-items:flex-start;line-height:20px;margin-bottom:10px}
.social{display:flex;gap:13px}
.social span{width:25px;height:25px;background:var(--white);border-radius:4px}
.footer-rule{position:absolute;left:88px;top:235px;width:1024px;height:1px;background:#333}
.copyright{position:absolute;top:260px;width:1200px;text-align:center;font-size:13px}
</style>
</head>
<body>

<header class="site-header">
  <div class="brand"><span class="brand-mark"></span><span class="brand-name">BREVLON</span></div>
  <nav class="main-nav"><span>Events</span><span>Expand</span><span>X</span><span>About</span><span>Connect</span></nav>
  <div class="login-btn">Login</div>
</header>
<svg class="abs" style="left:0;top:100px" width="1200" height="50" viewBox="0 0 1200 50">
  <polygon points="560,50 1200,10 1200,40 900,50" fill="var(--red)"/>
</svg>

<section class="hero">
  <div class="hero-art" role="img" aria-label="Hand lifting a floating cluster of glowing blue cubes"></div>
  <h1 class="hero-title">EXPAND YOUR BUSINESS</h1>
  <p class="hero-sub heading">It’s about our unique X Strategy</p>
  <div class="hero-dots"><span></span><span></span><span></span><span></span></div>
</section>
<svg class="abs" style="left:0;top:640px" width="1200" height="210" viewBox="0 0 1200 210">
  <polygon points="0,30 860,90 1200,95 1200,145 0,145" fill="var(--white)"/>
  <polygon points="0,30 0,145 860,95" fill="var(--purple)"/>
  <polygon points="1015,200 1060,120 1095,120 1050,200" fill="var(--purple-soft)"/>
  <polygon points="1070,200 1115,120 1160,120 1200,200" fill="var(--yellow-soft)"/>
</svg>

<!-- offer -->
<h2 class="section-title" style="top:868px;font-size:35px">What we offer you</h2>
<p class="section-sub" style="top:920px">Neque porro quisquam est dolorem</p>
<svg class="abs" style="left:65px;top:1105px" width="30" height="44" viewBox="0 0 30 44"><polyline points="24,2 6,22 24,42" fill="none" stroke="#999" stroke-width="2"/></svg>
<svg class="abs" style="left:1105px;top:1105px" width="30" height="44" viewBox="0 0 30 44"><polyline points="6,2 24,22 6,42" fill="none" stroke="#999" stroke-width="2"/></svg>

<div class="offer-item" style="left:110px;top:1005px">
  <div class="offer-icon">
    <svg class="tri" width="120" height="120" viewBox="0 0 120 120"><polygon points="0,0 120,0 60,70" fill="var(--yellow-soft)"/></svg>
    <div class="glyph" role="img" aria-label="Line icon of a head with a lightbulb held by two hands"></div>
  </div>
  <h3>EDUCATE</h3>
  <p>At BREVLON, we provide effective training and learning as the foundation for building a healthy, successful</p>
  <svg class="more" width="18" height="16" viewBox="0 0 18 16"><polyline points="2,2 9,8 16,2" fill="none" stroke="#222" stroke-width="2"/><polyline points="2,8 9,14 16,8" fill="none" stroke="#222" stroke-width="2"/></svg>
</div>
<div class="offer-item" style="left:470px;top:1005px">
  <div class="offer-icon">
    <svg class="tri" width="120" height="120" viewBox="0 0 120 120"><polygon points="0,0 120,0 60,70" fill="var(--yellow-soft)"/></svg>
    <div class="glyph" role="img" aria-label="Line icon of two people meeting at a computer"></div>
  </div>
  <h3>EQUIP</h3>
  <p>Through our connected ecosystem of companies, we’ll help find the right partners for equipping you to move</p>
  <svg class="more" width="18" height="16" viewBox="0 0 18 16"><polyline points="2,2 9,8 16,2" fill="none" stroke="#222" stroke-width="2"/><polyline points="2,8 9,14 16,8" fill="none" stroke="#222" stroke-width="2"/></svg>
</div>
<div class="offer-item" style="left:820px;top:1005px">
  <div class="offer-icon">
    <svg class="tri" width="120" height="120" viewBox="0 0 120 120"><polygon points="0,0 120,0 60,70" fill="var(--yellow-soft)"/></svg>
    <div class="glyph" role="img" aria-label="Line icon of a network hub above a laptop"></div>
  </div>
  <h3>EXCHANGE</h3>
  <p>We connect you with others who have successfully implemented our X Strategy to facilitate growth in their</p>
  <svg class="more" width="18" height="16" viewBox="0 0 18 16"><polyline points="2,2 9,8 16,2" fill="none" stroke="#222" stroke-width="2"/><polyline points="2,8 9,14 16,8" fill="none" stroke="#222" stroke-width="2"/></svg>
</div>

<!-- about -->
<section class="abs" style="left:0;top:1370px;width:1200px;height:530px">
  <div class="abs" style="inset:0;background:radial-gradient(circle at 50% 45%,#1d4a8f 0%,#0f2a5c 55%,#0a1d42 100%)" role="img" aria-label="Businessman facing tall upward arrows on a blue backdrop"></div>
  <svg class="abs" style="left:0;top:0" width="1200" height="530" viewBox="0 0 1200 530">
    <polygon points="0,0 1200,0 1200,5 500,15 0,0" fill="var(--white)"/>
    <polygon points="560,12 1200,0 1200,95" fill="var(--yellow)"/>
    <polygon points="0,445 950,440 0,530" fill="var(--yellow)"/>
    <polygon points="0,530 950,440 1200,430 1200,530" fill="var(--white)"/>
  </svg>
  <h2 class="section-title" style="top:125px;font-size:40px;color:var(--white)">About us</h2>
</section>
<p class="about-text">It is a long established fact that a reader will be distracted by the readable content of a page when looking at its layout. The point of using Lorem Ipsum is that it has a more-or-less normal distribution of letters, as opposed to using ‘Content here, content here’, making it look like readable English. Many desktop publishing packages and web page editors now use Lorem Ipsum as their default model text, and a search for ‘lorem ipsum’ will uncover many web sites still in their infancy The point of using Lorem Ipsum is that it has a more-or-less normal distribution of letters, as opposed to using</p>
<div class="pill-btn" style="left:530px;top:1738px;width:140px;height:36px;line-height:36px">Read More</div>
<svg class="abs" style="left:0;top:1895px" width="220" height="80" viewBox="0 0 220 80">
  <polygon points="0,80 45,0 80,0 35,80" fill="var(--purple-soft)"/>
  <polygon points="60,80 105,0 150,0 205,80" fill="var(--yellow-soft)"/>
</svg>

<!-- value -->
<h2 class="section-title" style="top:1995px;font-size:40px">X = VALUE</h2>
<p class="section-sub" style="top:2048px;font-size:19px">Neque porro quisquam est qui dolorem</p>
<div class="value-circle"><span class="brand-mark"></span><span class="brand-name">BREVLON</span></div>

<div class="value-icon" role="img" aria-label="Brain icon" style="left:138px;top:2170px;border:2px solid var(--accent-blue);border-radius:50%"></div>
<div class="value-item" style="left:200px;top:2162px"><h3 style="color:var(--accent-blue)">Mind</h3>Duis aute irure dolor<br>in reprehenderit in voluptate.<br>Exceptiur sint occaecat.</div>
<div class="value-icon" role="img" aria-label="Praying hands icon" style="left:132px;top:2328px;border:2px solid var(--soul);border-radius:50%"></div>
<div class="value-item" style="left:200px;top:2320px"><h3 style="color:var(--soul)">Soul</h3>Duis aute irure dolor<br>in reprehenderit in voluptate.<br>Exceptiur sint occaecat.</div>

<svg class="value-icon" style="left:1010px;top:2168px" viewBox="0 0 40 40"><path d="M20 35 L5 19 A8 8 0 0 1 20 9 A8 8 0 0 1 35 19 Z" fill="none" stroke="var(--red)" stroke-width="2"/></svg>
<div class="value-item right" style="left:715px;top:2162px"><h3 style="color:var(--red)">Heart</h3>Duis aute irure dolor<br>in reprehenderit in voluptate.<br>Exceptiur sint occaecat.</div>
<div class="value-icon" role="img" aria-label="Thumbs up icon" style="left:1010px;top:2325px;border:2px solid var(--strength);border-radius:6px"></div>
<div class="value-item right" style="left:715px;top:2320px"><h3 style="color:var(--strength)">Strength</h3>Duis aute irure dolor<br>in reprehenderit in voluptate.<br>Exceptiur sint occaecat.</div>

<!-- contact -->
<section class="abs" style="left:0;top:2530px;width:1200px;height:600px">
  <div class="abs" style="inset:0;background:radial-gradient(circle at 50% 40%,#1a2a44 0%,#0c1628 55%,#060d1a 100%)" role="img" aria-label="Silhouette of a businessman in a dim office"></div>
  <svg class="abs" style="left:0;top:0" width="1200" height="600" viewBox="0 0 1200 600">
    <polygon points="0,0 1200,0 1200,5 0,0" fill="var(--white)"/>
    <polygon points="0,20 1200,5 1200,8 480,75 0,110" fill="var(--purple)"/>
    <polygon points="0,0 1200,0 1200,5 0,20" fill="var(--white)"/>
    <polygon points="0,600 1200,490 1200,600" fill="var(--white)"/>
    <polygon points="700,560 1200,490 1200,530" fill="var(--purple)"/>
  </svg>
  <h2 class="section-title" style="top:145px;font-size:40px;color:var(--white)">Contact</h2>
</section>
<div class="field" style="left:218px;top:2785px;width:372px">Name</div>
<div class="field" style="left:608px;top:2785px;width:374px">Email id</div>
<div class="field" style="left:218px;top:2865px;width:764px">Message</div>
<div class="pill-btn" style="left:542px;top:2944px;width:116px;height:36px;line-height:36px">Submit</div>
<svg class="abs" style="left:1015px;top:3105px" width="185" height="85" viewBox="0 0 185 85">
  <polygon points="0,85 45,0 80,0 35,85" fill="var(--purple-soft)"/>
  <polygon points="60,85 105,0 150,0 185,60 185,85" fill="var(--yellow-soft)"/>
</svg>

<!-- events -->
<h2 class="section-title" style="top:3195px;font-size:40px">Events</h2>
<article class="event-card" style="left:88px;top:3285px">
  <div class="event-photo" role="img" aria-label="Businessman overlooking a city skyline" style="background:linear-gradient(180deg,#c7d2dc,#5f6b78)"></div>
  <div class="event-body"><div class="event-date">JAN 25,2019</div><h3>Dolorem ipsum quia dolor</h3><p>It has survived not only five centuries,<br>but also the leap into electronic</p><span class="red-btn">Read More</span></div>
</article>
<article class="event-card" style="left:438px;top:3285px">
  <div class="event-photo" role="img" aria-label="Businessman facing a rising growth chart" style="background:linear-gradient(180deg,#2f5d87,#16334f)"></div>
  <div class="event-body"><div class="event-date">JAN 25,2019</div><h3>Dolorem ipsum quia dolor</h3><p>It has survived not only five centuries,<br>but also the leap into electronic</p><span class="red-btn">Read More</span></div>
</article>
<article class="event-card" style="left:790px;top:3285px">
  <div class="event-photo" role="img" aria-label="Businessman in a suit holding a glowing icon" style="background:linear-gradient(180deg,#8ec6e6,#2f4e6e)"></div>
  <div class="event-body"><div class="event-date">JAN 25,2019</div><h3>Dolorem ipsum quia dolor</h3><p>It has survived not only five centuries,<br>but also the leap into electronic</p><span class="red-btn">Read More</span></div>
</article>

<svg class="abs" style="left:0;top:3715px" width="1200" height="80" viewBox="0 0 1200 80">
  <polygon points="0,5 820,80 0,80" fill="var(--yellow)"/>
  <polygon points="820,80 1200,45 1200,80" fill="#000"/>
</svg>

<footer class="site-footer">
  <div class="brand" style="left:100px;top:102px"><span class="brand-mark"></span><span class="brand-name" style="color:var(--white);font-size:28px">BREVLON</span></div>
  <div class="footer-col" style="left:385px">
    <h4>INFORMATION</h4>
    <ul><li>Privacy Policy</li><li>Your Account</li><li>Advanced Search</li><li>Contact Us</li></ul>
  </div>
  <div class="footer-col" style="left:632px">
    <h4>CONTACT US</h4>
    <div class="contact-line"><svg width="12" height="16" viewBox="0 0 12 16"><path d="M6 15 C2 9 1 7 1 5 A5 5 0 0 1 11 5 C11 7 10 9 6 15Z" fill="var(--yellow)"/><circle cx="6" cy="5" r="2" fill="#000"/></svg><span>410-B Harlow Court,<br>Linden Vale, FL 30000</span></div>
    <div class="contact-line"><svg width="12" height="14" viewBox="0 0 12 14"><path d="M2 1 L5 1 L6 4 L4 6 C5 8 6 9 8 10 L10 8 L12 9 L12 12 C6 13 0 7 2 1Z" fill="var(--yellow)"/></svg><span>0100 555 0142</span></div>
    <div class="contact-line"><svg width="14" height="12" viewBox="0 0 14 12"><rect x="0" y="1" width="14" height="10" fill="var(--yellow)"/><polyline points="0,1 7,7 14,1" fill="none" stroke="#000" stroke-width="1.2"/></svg><span>hello@brevlon.example</span></div>
  </div>
  <div class="footer-col" style="left:910px">
    <h4>FOLLOW US OUT THERE</h4>
    <div class="social"><span></span><span></span><span></span><span></span></div>
  </div>
  <div class="footer-rule"></div>
  <p class="copyright">Copyright © 2018 All Rights Reserved</p>
</footer>

</body>
</html>
```